Harrowmere Freight, Project

Company Profile
Harrowmere Freight Sdn Bhd is a well established and experienced freight forwarder in Kuala Lumpur, Malaysia. We specialize in air and sea forwarding, Custom Brokerage and regulatory compliance services, inland transportation,
overseas freighting and warehousing and distribution management. With our dedicated qualified and experienced professionals, we are fully committed to serving our clients.

Our Mission
Based on the motto “Quick, Reliable and Polite”, Harrowmere Freight is dedicated to upholding the following three points corporate philosophy:
1. Adhering to the principle that “the customer always comes first”.
2. Contributing to the development of the local community.
3. Making it our duty to be responsible and sincere.

Our Edge
• One-Stop Logistics Solutions
• Extensive Network Throughout Malaysia
• Highly Qualified and Experienced Pool of Professionals
• Comprehensive IT Solutions
• Innovative and Customer-focused Solutions
• Flexible and Consistent in Managing Exceptions
• Total Supply Chain Visibility

Target Market(s)

We sell the logistics services to all the industry in Malaysia. (ONE Stop Logistics Solutions)

Industry/Entity Type

Logistic

Contact Information for Business Card

I want the back of the card to be white with the logo and slogan. i would like to see the logo on the front with the general info.

Requirements
Must have
• Name, Title, Office, Cell, Fax, Email, Address, Website
Nice to have
• Modern Design Business Card

```html
<!DOCTYPE html>
<html lang="en">
<head>
<meta charset="utf-8">
<title>Harrowmere Freight – Business Card</title>
<link href="https://fonts.googleapis.com/css2?family=Open+Sans:wght@400;600;700&display=swap" rel="stylesheet">
<style>
  :root {
    --bg: #ecebe8;
    --card-grey: #6b6c6e;
    --card-grey-dark: #58595b;
    --white: #ffffff;
    --ink: #4a4b4d;
    --ink-soft: #77787b;
    --blue: #2a9fd8;
    --band-grey: #6d6e70;
    --band-light: #d9dadb;
  }
  * { margin: 0; padding: 0; box-sizing: border-box; }
  html, body { width: 1200px; height: 950px; overflow: hidden; }
  body {
    background: var(--bg);
    font-family: "Open Sans", Arial, sans-serif;
    position: relative;
  }
  .card {
    position: absolute;
    width: 700px;
    height: 400px;
    overflow: hidden;
    box-shadow: 0 6px 18px rgba(0,0,0,0.18);
  }

  /* Back of card */
  .card-back {
    left: 120px; top: 60px;
    background: linear-gradient(135deg, var(--card-grey) 0%, var(--card-grey-dark) 100%);
    color: var(--white);
  }
  .services {
    position: absolute; left: 46px; top: 120px;
  }
  .services-title { font-size: 19px; font-weight: 700; margin-bottom: 8px; }
  .services-list { list-style: none; font-size: 15px; line-height: 20px; }
  .services-tagline { font-size: 15px; font-weight: 700; margin-top: 4px; letter-spacing: 0.3px; }
  .back-brand {
    position: absolute; left: 400px; top: 150px; width: 260px;
    display: flex; align-items: center; gap: 14px;
  }
  .back-brand .dot { width: 22px; height: 22px; border-radius: 50%; background: var(--white); flex: none; }
  .back-brand .name { font-size: 34px; font-weight: 600; line-height: 40px; color: var(--white); }

  /* Front of card */
  .card-front {
    left: 380px; top: 490px;
    background: var(--white);
    color: var(--ink);
  }
  .front-brand {
    position: absolute; left: 40px; top: 200px; width: 260px;
    display: flex; align-items: center; gap: 12px;
  }
  .front-brand .square { width: 20px; height: 20px; background: var(--blue); flex: none; }
  .front-brand .name { font-size: 32px; font-weight: 600; line-height: 36px; color: var(--ink); }

  .person { position: absolute; left: 330px; top: 44px; }
  .person-name { font-size: 25px; font-weight: 600; color: var(--blue); line-height: 30px; }
  .person-title { font-size: 14px; color: var(--ink-soft); margin-bottom: 10px; }
  .company { font-size: 12.5px; font-weight: 700; color: var(--ink); }
  .address { font-size: 13px; line-height: 18px; color: var(--ink); }
  .contacts { list-style: none; margin-top: 6px; font-size: 13px; line-height: 20px; }
  .contacts li { display: flex; align-items: center; gap: 8px; }
  .contacts svg { width: 12px; height: 12px; fill: var(--blue); flex: none; }

  .accent-bar { position: absolute; right: 0; top: 228px; }
  .mini-mark { position: absolute; right: 30px; top: 268px; width: 26px; height: 26px; border-radius: 50%; background: var(--blue); }
  .footer-band { position: absolute; left: 0; bottom: 0; width: 700px; height: 62px; }
  .website {
    position: absolute; left: 0; bottom: 14px; width: 700px; text-align: center;
    font-size: 17px; letter-spacing: 4px; color: var(--white);
  }
</style>
</head>
<body>

  <section class="card card-back" aria-label="Business card back">
    <div class="services">
      <h2 class="services-title">We’re Specialize In</h2>
      <ul class="services-list">
        <li>International Shipping (Air / Sea)</li>
        <li>Consolidation - NVOCC</li>
        <li>Project Management</li>
        <li>Supply Chain Management</li>
        <li>Tax Exemption Consultancy</li>
        <li>Custom Brokerage</li>
        <li>Transportation / Haulage</li>
        <li>Warehousing</li>
        <li>Packing</li>
        <li>Marine Insurance</li>
        <li>Distribution</li>
        <li>Door to Door</li>
      </ul>
      <p class="services-tagline">ONE STOP LOGISTICS SOLUTIONS</p>
    </div>
    <div class="back-brand">
      <span class="dot"></span>
      <span class="name">Harrowmere Freight</span>
    </div>
  </section>

  <section class="card card-front" aria-label="Business card front">
    <div class="front-brand">
      <span class="square"></span>
      <span class="name">Harrowmere Freight</span>
    </div>

    <div class="person">
      <h1 class="person-name">Faizal Rahmat</h1>
      <p class="person-title">Managing Director</p>
      <p class="company">HARROWMERE FREIGHT SDN. BHD. (1248637-K)</p>
      <p class="address">No.14B, 2nd Floor, Jalan Seri Perdana 3,<br>Taman Perdana Jaya, 41050 Klang,<br>Selangor Darul Ehsan, Malaysia.<br>(603) 3340 2615 / 2616</p>
      <ul class="contacts">
        <li><svg viewBox="0 0 12 12"><path d="M2.5 0.5 L4.5 0.5 L5.3 3.2 L4 4.3 C4.7 5.8 6.2 7.3 7.7 8 L8.8 6.7 L11.5 7.5 L11.5 9.5 C11.5 10.6 10.6 11.5 9.5 11.5 C4.5 11.2 0.8 7.5 0.5 2.5 C0.5 1.4 1.4 0.5 2.5 0.5 Z"/></svg>(603) 3340 2615</li>
        <li><svg viewBox="0 0 12 12"><path d="M3 0 H9 A1 1 0 0 1 10 1 V11 A1 1 0 0 1 9 12 H3 A1 1 0 0 1 2 11 V1 A1 1 0 0 1 3 0 Z M3.5 1.5 V9 H8.5 V1.5 Z M5.5 10 H6.5 V11 H5.5 Z"/></svg>+6012-480 7731</li>
        <li><svg viewBox="0 0 12 12"><path d="M3 0 H9 V4 H3 Z M1 4.5 H11 A1 1 0 0 1 12 5.5 V10 H10 V12 H2 V10 H0 V5.5 A1 1 0 0 1 1 4.5 Z M3 8 V11 H9 V8 Z"/></svg>(603) 3340 2619</li>
        <li><svg viewBox="0 0 12 12"><path d="M0 2 H12 V10 H0 Z M0.8 2.6 L6 6.6 L11.2 2.6 V3.6 L6 7.6 L0.8 3.6 Z" fill-rule="evenodd"/></svg>faizal@harrowmere.com.my</li>
      </ul>
    </div>

    <svg class="accent-bar" width="170" height="14" viewBox="0 0 170 14" aria-hidden="true">
      <polygon points="14,0 170,0 170,14 0,14" fill="var(--blue)"/>
    </svg>
    <span class="mini-mark"></span>

    <svg class="footer-band" viewBox="0 0 700 62" aria-hidden="true">
      <rect x="0" y="0" width="700" height="8" fill="var(--band-light)"/>
      <rect x="0" y="12" width="700" height="50" fill="var(--band-grey)"/>
    </svg>
    <p class="website">www.harrowmere.com.my</p>
  </section>

</body>
</html>
```